Clear Plastic Card Design

I am looking to have a business card designed from my logo icon. I am looking to match the style of a different business card I have attached in the files.
Looking for a card that is plastic, with layers of transparency in the shape of my logo icon (also attached in the files) - not a circle like the other card. The winning design will incorporate the red icon logo on the front and back and include the charity's name, "Light for the Weary Souls" in the same or similar font, as well as an email and phone number. For now, use the email: email@lightfortheweary-mail.org and the phone number 555-382-7194.
We like how the sample business card has transparency, partial and full opacity layers and a matching color scheme. Files will need to be in vector so that our business card printing company can work with it.
UPDATE:
We've some excellent designs in, thank you everyone! I got an early review from the owner, and he requested a minor redirect to find his perfect design. He wants the design to stand out by NOT being a rectangle. Try instead a circle, square, or best yet - something that falls in the outline of the logo icon, either fully or partially. Thank you, everyone!
Light for the Weary Souls text should be incorporated as well as a phone and email.

```html
<!DOCTYPE html>
<html lang="en">
<head>
<meta charset="utf-8">
<title>Light for the Weary Souls – Die-cut Cards</title>
<link rel="stylesheet" href="https://fonts.googleapis.com/css2?family=Montserrat:wght@400;500;700;800&family=Urbanist:wght@400;500&display=swap">
<style>
  :root {
    --stage: #e4e4e4;
    --card-white: #ffffff;
    --brand-red: #d0202a;
    --brand-red-deep: #c21a24;
    --brand-orange: #ef6a24;
    --brand-pink: #d91c4a;
    --ink: #1c1c1c;
    --card-edge: #cfcfcf;
  }
  * { box-sizing: border-box; margin: 0; padding: 0; }
  html, body { width: 1079px; height: 1200px; overflow: hidden; }
  body { background: var(--stage); position: relative; font-family: "Montserrat", sans-serif; }

  .card { position: absolute; inset: 0; }
  .card-block, .card-panel { position: absolute; }

  /* Front card (white) */
  .front .card-block {
    left: 461px; top: 62px; width: 494px; height: 380px;
    background: var(--card-white); border-radius: 44px;
    box-shadow: 0 0 0 1px var(--card-edge);
  }
  .front .brand-square {
    position: absolute; left: 18px; top: 18px; right: 18px; bottom: 18px;
    border-radius: 30px;
    background: linear-gradient(150deg, var(--brand-orange) 0%, #e4402a 45%, var(--brand-pink) 75%, var(--brand-red-deep) 100%);
  }
  .front .brand-name {
    position: absolute; left: 52px; top: 52px; width: 380px;
    font-family: "Montserrat", sans-serif; font-weight: 800; font-size: 44px; line-height: 1.12;
    color: var(--card-white);
  }
  .front .card-panel {
    left: 129px; top: 326px; width: 566px; height: 232px;
    background: var(--card-white); border-radius: 16px;
    box-shadow: 0 0 0 1px var(--card-edge);
    padding: 24px 20px;
  }
  .front .org-title {
    font-weight: 700; font-size: 23px; line-height: 1.3; letter-spacing: 0.3px;
    color: var(--brand-red); text-transform: uppercase;
  }
  .contact-list { list-style: none; margin-top: 34px; }
  .contact-list li {
    display: flex; align-items: center; gap: 14px;
    font-weight: 400; font-size: 20px; color: var(--ink); margin-bottom: 14px;
  }
  .contact-list svg { width: 18px; height: 18px; fill: var(--brand-red); flex: none; }

  /* Back card (red) */
  .back .card-block {
    left: 461px; top: 607px; width: 494px; height: 395px;
    background: var(--brand-red); border-radius: 48px;
  }
  .back .brand-square {
    position: absolute; left: 22px; top: 22px; right: 22px; bottom: 22px;
    border-radius: 30px; background: var(--brand-red-deep);
  }
  .back .brand-name {
    position: absolute; left: 56px; top: 56px; width: 380px;
    font-family: "Montserrat", sans-serif; font-weight: 800; font-size: 44px; line-height: 1.12;
    color: var(--card-white);
  }
  .back .card-panel {
    left: 129px; top: 866px; width: 566px; height: 220px;
    background: var(--brand-red); border-radius: 18px;
    padding: 40px 40px;
  }
  .back .org-title {
    font-family: "Urbanist", sans-serif; font-weight: 400; font-size: 60px; line-height: 1.05;
    color: var(--card-white);
  }
</style>
</head>
<body>

  <section class="card front" aria-label="Card front">
    <div class="card-block">
      <div class="brand-square"></div>
      <p class="brand-name">Light for the Weary Souls</p>
    </div>
    <div class="card-panel">
      <h1 class="org-title">Light for<br>the Weary Souls</h1>
      <ul class="contact-list">
        <li>
          <svg viewBox="0 0 24 24" aria-hidden="true"><path d="M6.6 10.8a15.1 15.1 0 0 0 6.6 6.6l2.2-2.2c.3-.3.7-.4 1-.2 1.1.4 2.3.6 3.6.6.6 0 1 .4 1 1V20c0 .6-.4 1-1 1A17 17 0 0 1 3 4c0-.6.4-1 1-1h3.5c.6 0 1 .4 1 1 0 1.3.2 2.5.6 3.6.1.3 0 .7-.2 1z"/></svg>
          555-382-7194
        </li>
        <li>
          <svg viewBox="0 0 24 24" aria-hidden="true"><path d="M3 5h18c.6 0 1 .4 1 1v12c0 .6-.4 1-1 1H3c-.6 0-1-.4-1-1V6c0-.6.4-1 1-1zm9 7 8-5H4z"/></svg>
          email@lightfortheweary-mail.org
        </li>
      </ul>
    </div>
  </section>

  <section class="card back" aria-label="Card back">
    <div class="card-block">
      <div class="brand-square"></div>
      <p class="brand-name">Light for the Weary Souls</p>
    </div>
    <div class="card-panel">
      <h2 class="org-title">Light for the<br>Weary Souls</h2>
    </div>
  </section>

</body>
</html>
```